Multiple website banners for a shopify theme

I need custom designed banners for a destributor webpage.

We will be selling products in our local store from a supplier https://glimmorabath.co.uk (you can get the ideas from their site).

We need custom desings:
- 2-3x 1920x745
- 1x 960x960
- 2x 480x480
- 1x 960*480
All of theme need to nicely fit together as shown in the uploaded layout screenshot (website_banner_layout).
In Google drive link there are products pictures which must be used in the banners.

https://files.quorvane.net/share/folders/7TkpWq2LmXe9VbNa4cHsYdRuF3jGz8Qo?mode=view

Kids, Cosmetics market

Cosmetics

• Playful elements

```html
<!DOCTYPE html>
<html lang="en">
<head>
<meta charset="utf-8">
<title>Glimmora Bath – Website Banner Set</title>
<link rel="stylesheet" href="https://fonts.googleapis.com/css2?family=Poppins:wght@400;500;600;700;800&display=swap">
<style>
  :root {
    --board: #f0f0f0;
    --label: #2a2a2a;
    --pink-soft: #f7a8cf;
    --pink-light: #fbc4de;
    --magenta: #f0449a;
    --magenta-deep: #e2318a;
    --purple: #8a5bc9;
    --purple-deep: #7040b0;
    --ink: #2b0b4f;
    --white: #ffffff;
    --leaf: #2f8a2a;
    --leaf-light: #6cc04a;
  }
  * { box-sizing: border-box; margin: 0; padding: 0; }
  html, body { width: 1061px; height: 1200px; overflow: hidden; background: var(--board); }
  body { position: relative; font-family: "Poppins", sans-serif; color: var(--ink); }

  .size-label { position: absolute; font-size: 22px; font-weight: 400; color: var(--label); transform: translateX(-50%); white-space: nowrap; letter-spacing: 0.5px; }

  .banner { position: absolute; overflow: hidden; box-shadow: 0 3px 6px rgba(0,0,0,0.12); }
  .banner > svg.bg { position: absolute; inset: 0; width: 100%; height: 100%; }

  .brand { position: absolute; display: flex; align-items: center; gap: 6px; font-weight: 700; white-space: nowrap; color: var(--white); }
  .brand .dot { border-radius: 50%; background: var(--white); flex: none; }
  .brand.on-white { color: var(--magenta); }
  .brand.on-white .dot { background: var(--magenta); }

  .headline { position: absolute; font-weight: 800; line-height: 1.02; letter-spacing: -0.5px; white-space: nowrap; }
  .lead { position: absolute; font-weight: 500; line-height: 1.22; white-space: nowrap; }

  .btn { position: absolute; display: flex; align-items: center; justify-content: center; color: var(--white); border-radius: 999px; background: linear-gradient(90deg, var(--magenta-deep), var(--purple-deep)); border: 1.5px solid var(--white); font-weight: 400; white-space: nowrap; }
  .btn.solid-purple { background: var(--purple); border: none; }

  /* Soft product and foliage areas */
  .blob { position: absolute; border-radius: 50%; }
  .leaves { position: absolute; border-radius: 50%; background: radial-gradient(closest-side, var(--leaf) 0%, var(--leaf-light) 55%, rgba(108,192,74,0) 100%); }

  /* Hero 1920x745 */
  .hero { left: 67px; top: 123px; width: 925px; height: 359px; }
  /* Square 960x960 */
  .square { left: 68px; top: 546px; width: 459px; height: 459px; }
  /* Tiles 480x480 */
  .tile { top: 546px; width: 221px; height: 221px; }
  .tile.pink-top { left: 538px; }
  .tile.purple-top { left: 774px; }
  .tile .headline { left: 0; width: 100%; text-align: center; font-size: 16.5px; color: var(--white); font-weight: 700; }
  .tile .fine { position: absolute; left: 0; width: 100%; text-align: center; font-size: 5.5px; color: var(--white); line-height: 1.25; padding: 0 40px; }
  .tile .btn { font-size: 8px; border-width: 1px; }
  /* Wide 960x480 */
  .wide { left: 538px; top: 777px; width: 456px; height: 228px; background: var(--white); }
</style>
</head>
<body>

  <div class="size-label" style="left:547px; top:90px;">1920x745 PX</div>
  <div class="size-label" style="left:643px; top:503px;">480x480PX</div>
  <div class="size-label" style="left:879px; top:503px;">480x480PX</div>
  <div class="size-label" style="left:297px; top:1031px;">960x960PX</div>
  <div class="size-label" style="left:769px; top:1025px;">960x480PX</div>

  <!-- Hero banner -->
  <section class="banner hero">
    <svg class="bg" viewBox="0 0 925 359" preserveAspectRatio="none" aria-hidden="true">
      <defs>
        <linearGradient id="heroPink" x1="0" y1="0" x2="1" y2="1">
          <stop offset="0" stop-color="#f9b3d5"/>
          <stop offset="0.5" stop-color="#f7a3cc"/>
          <stop offset="1" stop-color="#f59cc8"/>
        </linearGradient>
      </defs>
      <rect width="925" height="359" fill="url(#heroPink)"/>
      <path d="M620 0 H925 V200 C850 160 720 120 660 60 Z" fill="var(--magenta)"/>
      <path d="M648 0 C690 40 760 110 925 195" fill="none" stroke="var(--white)" stroke-width="2"/>
    </svg>
    <div class="blob" role="img" aria-label="Background texture: soft pink wavy swirl pattern" style="left:0; top:0; width:520px; height:359px; border-radius:0; background: radial-gradient(ellipse at 30% 40%, rgba(255,214,233,0.55), rgba(255,214,233,0) 70%);"></div>
    <div class="leaves" role="img" aria-label="Palm leaves" style="left:750px; top:0; width:180px; height:210px;"></div>
    <div class="blob" role="img" aria-label="Iced bath bomb topped with cream swirls, pearls and a red bow" style="left:540px; top:22px; width:255px; height:285px; background: radial-gradient(closest-side, #fffaf4 0%, #f7e6ec 50%, #e9a9c6 80%, rgba(233,169,198,0) 100%);"></div>
    <div class="blob" role="img" aria-label="Unicorn candle in a glass" style="left:474px; top:140px; width:124px; height:175px; background: radial-gradient(closest-side, #f3c2db 0%, #e38fba 60%, rgba(227,143,186,0) 100%);"></div>
    <div class="blob" role="img" aria-label="Raspberries" style="left:543px; top:232px; width:122px; height:92px; background: radial-gradient(closest-side, #d3275f 0%, #e24d7f 60%, rgba(226,77,127,0) 100%);"></div>
    <div class="blob" role="img" aria-label="Donut lip scrub jar with its lid" style="left:698px; top:168px; width:182px; height:150px; background: radial-gradient(closest-side, #ffffff 0%, #f8d9e8 45%, #ef6fac 80%, rgba(239,111,172,0) 100%);"></div>

    <div class="brand" style="left:38px; top:40px; font-size:24px;"><span class="dot" style="width:20px;height:20px;"></span>Glimmora Bath</div>
    <h1 class="headline" style="left:38px; top:112px; font-size:46px;">Love Your Skin<br>You’re in!</h1>
    <p class="lead" style="left:38px; top:204px; font-size:15.5px;">Our gorgeous Body Buffers are a really easy way<br>to buff and shine your skin in the shower</p>
    <a class="btn" style="left:42px; top:254px; width:166px; height:32px; font-size:21px;">SHOP NOW</a>
  </section>

  <!-- Square banner -->
  <section class="banner square">
    <svg class="bg" viewBox="0 0 459 459" preserveAspectRatio="none" aria-hidden="true">
      <defs>
        <linearGradient id="sqPink" x1="0" y1="0" x2="1" y2="1">
          <stop offset="0" stop-color="#f9b3d5"/>
          <stop offset="1" stop-color="#f59cc8"/>
        </linearGradient>
      </defs>
      <rect width="459" height="459" fill="url(#sqPink)"/>
      <path d="M0 418 C60 330 150 300 230 300 C310 300 400 330 459 418 V459 H0 Z" fill="var(--magenta)"/>
      <path d="M0 408 C60 322 150 292 230 292 C310 292 400 322 459 408" fill="none" stroke="var(--white)" stroke-width="2"/>
    </svg>
    <div class="leaves" role="img" aria-label="Palm leaves" style="left:340px; top:170px; width:140px; height:170px;"></div>
    <div class="blob" role="img" aria-label="Wrapped flowery gift pack with a red ribbon" style="left:98px; top:208px; width:190px; height:130px; background: radial-gradient(closest-side, #f6e4ef 0%, #e9b6d2 60%, rgba(233,182,210,0) 100%);"></div>
    <div class="blob" role="img" aria-label="Cake-style bath bomb and a white bath bomb" style="left:262px; top:244px; width:82px; height:115px; background: radial-gradient(closest-side, #fbe9a8 0%, #f3cf6a 55%, rgba(243,207,106,0) 100%);"></div>
    <div class="blob" role="img" aria-label="Star soaps, lime, raspberries, body butter tub and mangoes" style="left:62px; top:318px; width:345px; height:78px; background: radial-gradient(closest-side, #f6b04a 0%, #ec7c8f 45%, #b7df6a 75%, rgba(183,223,106,0) 100%);"></div>

    <div class="brand" style="left:50%; top:38px; transform:translateX(-50%); font-size:22px;"><span class="dot" style="width:18px;height:18px;"></span>Glimmora Bath</div>
    <h2 class="headline" style="left:0; width:100%; text-align:center; top:97px; font-size:36.5px;">The Flawsome<br>Gift Pack is Back!</h2>
    <p class="lead" style="left:0; width:100%; text-align:center; top:176px; font-size:13px; font-weight:400;">Save your skin and save the planet with<br>our flawsome gift pack.</p>
    <a class="btn" style="left:147px; top:402px; width:165px; height:32px; font-size:21px;">SHOP NOW</a>
  </section>

  <!-- Tile: pink -->
  <section class="banner tile pink-top">
    <svg class="bg" viewBox="0 0 221 221" preserveAspectRatio="none" aria-hidden="true">
      <rect width="221" height="221" fill="#f6f6f6"/>
      <path d="M0 0 H221 V62 C200 98 160 112 110 112 C60 112 20 98 0 62 Z" fill="var(--magenta)"/>
      <path d="M0 64 C20 102 60 117 110 117 C160 117 200 102 221 64" fill="none" stroke="var(--magenta)" stroke-width="1.2"/>
      <rect y="218" width="221" height="3" fill="var(--purple)"/>
    </svg>
    <div class="leaves" role="img" aria-label="Palm leaves" style="left:170px; top:95px; width:60px; height:70px;"></div>
    <div class="blob" role="img" aria-label="Pink cocktail umbrella" style="left:14px; top:100px; width:48px; height:42px; background: radial-gradient(closest-side, #f36aaa 0%, rgba(243,106,170,0) 100%);"></div>
    <div class="blob" role="img" aria-label="Soap bars, shower gel bottle and soap tin" style="left:20px; top:118px; width:185px; height:78px; background: radial-gradient(closest-side, #f2e5d8 0%, #e6b2c4 55%, rgba(230,178,196,0) 100%);"></div>
    <div class="blob" role="img" aria-label="Toy duck and lavender sprigs" style="left:40px; top:165px; width:100px; height:48px; background: radial-gradient(closest-side, #8267c4 0%, #b9a3e3 55%, rgba(185,163,227,0) 100%);"></div>

    <div class="brand" style="left:50%; top:12px; transform:translateX(-50%); font-size:11px;"><span class="dot" style="width:9px;height:9px;"></span>Glimmora Bath</div>
    <h3 class="headline" style="top:46px;">New Vegan<br>Friendly Shops</h3>
    <p class="fine" style="top:87px;">Our handmade shops are mild have a natural</p>
    <a class="btn" style="left:136px; top:192px; width:60px; height:11px;">SHOP NOW</a>
  </section>

  <!-- Tile: purple -->
  <section class="banner tile purple-top">
    <svg class="bg" viewBox="0 0 221 221" preserveAspectRatio="none" aria-hidden="true">
      <rect width="221" height="221" fill="#f6f6f6"/>
      <path d="M0 0 H221 V62 C200 98 160 112 110 112 C60 112 20 98 0 62 Z" fill="var(--purple)"/>
      <path d="M0 64 C20 102 60 117 110 117 C160 117 200 102 221 64" fill="none" stroke="var(--purple)" stroke-width="1.2"/>
      <rect y="218" width="221" height="3" fill="var(--magenta)"/>
    </svg>
    <div class="blob" role="img" aria-label="Pink cocktail umbrella" style="left:160px; top:100px; width:50px; height:42px; background: radial-gradient(closest-side, #f36aaa 0%, rgba(243,106,170,0) 100%);"></div>
    <div class="blob" role="img" aria-label="Purple soap bar, blue soap bottle and soap tin" style="left:30px; top:112px; width:175px; height:80px; background: radial-gradient(closest-side, #a78fd6 0%, #7ea3d2 50%, rgba(126,163,210,0) 100%);"></div>
    <div class="blob" role="img" aria-label="Toy duck, scrub and lavender sprigs" style="left:20px; top:160px; width:120px; height:52px; background: radial-gradient(closest-side, #8267c4 0%, #c9b7a0 55%, rgba(201,183,160,0) 100%);"></div>

    <div class="brand" style="left:50%; top:12px; transform:translateX(-50%); font-size:11px;"><span class="dot" style="width:9px;height:9px;"></span>Glimmora Bath</div>
    <h3 class="headline" style="top:46px;">New Vegan<br>Friendly Shops</h3>
    <p class="fine" style="top:85px; padding:0 36px;">Our handmade shops are mild, have a natural ph and gently cleanse with pure essential oils!</p>
    <a class="btn solid-purple" style="left:140px; top:189px; width:60px; height:11px;">SHOP NOW</a>
  </section>

  <!-- Wide banner -->
  <section class="banner wide">
    <svg class="bg" viewBox="0 0 456 228" preserveAspectRatio="none" aria-hidden="true">
      <rect width="456" height="228" fill="var(--white)"/>
      <path d="M214 0 H456 V140 C400 120 330 90 280 60 C250 40 225 20 214 0 Z" fill="var(--purple)"/>
    </svg>
    <div class="leaves" role="img" aria-label="Palm leaves" style="left:350px; top:0; width:110px; height:95px;"></div>
    <div class="blob" role="img" aria-label="Hand cream tube" style="left:244px; top:16px; width:56px; height:80px; background: radial-gradient(closest-side, #fff4e6 0%, #f5c8b2 60%, rgba(245,200,178,0) 100%);"></div>
    <div class="blob" role="img" aria-label="Purple bath bomb" style="left:282px; top:42px; width:100px; height:100px; background: radial-gradient(closest-side, #d7a6ef 0%, #b37ae0 65%, rgba(179,122,224,0) 100%);"></div>
    <div class="blob" role="img" aria-label="Polka dot candles" style="left:203px; top:88px; width:130px; height:135px; background: radial-gradient(closest-side, #ffffff 0%, #dbe7f6 55%, rgba(219,231,246,0) 100%);"></div>
    <div class="blob" role="img" aria-label="Raspberries and avocado" style="left:210px; top:138px; width:170px; height:60px; background: radial-gradient(closest-side, #d9306a 0%, #9fbf4a 60%, rgba(159,191,74,0) 100%);"></div>
    <div class="blob" role="img" aria-label="Pink round soap" style="left:350px; top:100px; width:90px; height:94px; background: radial-gradient(closest-side, #f794c4 0%, #ef6fac 65%, rgba(239,111,172,0) 100%);"></div>

    <div class="brand on-white" style="left:20px; top:44px; font-size:18px;"><span class="dot" style="width:16px;height:16px;"></span>Glimmora Bath</div>
    <h2 class="headline" style="left:20px; top:86px; font-size:31px; color:var(--magenta);">Get It While<br>It’s Hot!</h2>
    <p class="lead" style="left:21px; top:148px; font-size:18px; font-weight:700; color:var(--ink);">UP TO 50% OFF</p>
    <a class="btn solid-purple" style="left:21px; top:174px; width:107px; height:19px; font-size:13px;">SHOP NOW</a>
  </section>

</body>
</html>
```